Business Card (double-sided) and Stationary Design for dental office

1) Business Card Design: We need a business card design for a dental specialty office.
Texts should contain:
The name of our office "Brindle Oaks Orthodontics"
Tagline: "Specialist in Orthodontic and Maxillofacial Orthopedics"
Tag line: "Creating "Tolvering" smiles for Children and Adults"
Doctor name: "Doctor Name"
Office Address:
"123 Street Name
City, State Zip code"
Office email address: office@brindleoaksortho.com
Website: www.brindleoaksortho.com

We will provide the full office address once the design is selected
Theme: beach, paradise, coastal, wave
We would like to have some creativity in design. Some acceptable ideas: front page: logo and office name. Back page: more detail information, and map to office in form of an island. Please see sample from our other location, but you DON'T HAVE TO USE OR COPY THE SAME CONCEPT.

IF POSSIBLE, PLEASE SUBMIT AT LEAST TWO CONCEPTS: ONE WITH THE BACK LOOKING SIMILAR TO WHAT IS IN THE SAMPLE, AND ONE DIFFERENT.

Color: designer to choose. We have different shade of blues and sand color in our office. Please see logo.

2) Please also design a matching set of stationary that compliment the business card and our logo.

Target Market(s)

Dental

Contact Information for Business Card

See descriptions

Font styles to use
Other font styles liked:
• Matching texts in logo

Colors
0054AA
0677BA
7BADD7
CADEEF
E8F1F8
0094D4
00A9DD
6FCCEA
C7EBF8
E9F6FB
00AB8E
00BBA5
67D7C9
C6EFE9
E9F9F6

Requirements
Must have
• Double-sided
Nice to have
• Beach coastal theme
Should not have
• Any shape or drawing of of tooth or teeth. We don’t need these. You don't necessarily have to just cut and paste the logo art and text as a whole, you have the liberty to rearrange the text.

```html
<!DOCTYPE html>
<html lang="en">
<head>
<meta charset="utf-8">
<title>Brindle Oaks Orthodontics – Business Card</title>
<link href="https://fonts.googleapis.com/css2?family=Comic+Neue:ital,wght@0,700;1,700&family=Roboto:wght@400&family=Roboto+Condensed:ital,wght@0,700;1,700&display=swap" rel="stylesheet">
<style>
  :root {
    --backdrop: #e4e4e4;
    --card-white: #ffffff;
    --teal-deep: #3a8aa3;
    --teal-mid: #4e9fb5;
    --teal-light: #5aaec2;
    --mint: #7fd0bd;
    --text-grey: #555c60;
    --brown: #3b1d10;
    --sky-top: #5db9f3;
    --sky-low: #c4e6fa;
    --sea-deep: #1495d6;
    --sea-light: #5ec6ef;
    --sand-light: #f5cc85;
    --sand-deep: #e8a353;
  }
  * { margin: 0; padding: 0; box-sizing: border-box; }
  html, body { width: 1200px; height: 1200px; overflow: hidden; }
  body { background: var(--backdrop); position: relative; font-family: 'Roboto', sans-serif; }

  .card { position: absolute; left: 262px; width: 686px; height: 392px; border-radius: 22px; overflow: hidden; }
  .card-front { top: 165px; background: var(--card-white); }
  .card-back { top: 653px; }

  /* front */
  .brand-mark { position: absolute; left: 270px; top: 36px; width: 102px; height: 102px; border-radius: 50%; background: var(--teal-light); }
  .brand-name { position: absolute; left: 0; width: 642px; top: 144px; text-align: center; font-family: 'Comic Neue', sans-serif; font-weight: 700; font-size: 30px; color: var(--teal-deep); }
  .brand-sub { position: absolute; left: 0; width: 642px; top: 180px; text-align: center; font-family: 'Comic Neue', sans-serif; font-weight: 700; font-size: 13px; letter-spacing: 1.6px; color: var(--mint); }
  .doctor-name { position: absolute; left: 120px; width: 180px; top: 248px; text-align: right; font-family: 'Comic Neue', sans-serif; font-weight: 700; font-size: 23px; color: var(--teal-deep); }
  .divider { position: absolute; left: 321px; top: 219px; width: 1px; height: 89px; background: #cfd6d8; }
  .contact { position: absolute; left: 344px; top: 222px; list-style: none; font-size: 15.5px; color: var(--text-grey); line-height: 19px; }
  .contact li { display: flex; align-items: flex-start; gap: 6px; margin-bottom: 5px; }
  .contact svg { width: 13px; height: 13px; margin-top: 3px; flex: none; fill: var(--teal-deep); }
  .wave { position: absolute; left: 0; top: 280px; width: 686px; height: 112px; }
  .website { position: absolute; left: 0; width: 686px; top: 358px; text-align: center; color: #fff; font-size: 15.5px; letter-spacing: 4.2px; }

  /* back */
  .beach-scene { position: absolute; inset: 0; background: linear-gradient(180deg, var(--sky-top) 0%, var(--sky-low) 44%, var(--sea-deep) 47%, var(--sea-light) 70%, var(--sand-light) 76%, var(--sand-deep) 100%); }
  .back-brand { position: absolute; left: 90px; width: 200px; top: 118px; text-align: center; font-family: 'Comic Neue', sans-serif; font-weight: 700; font-size: 23px; color: var(--brown); white-space: nowrap; }
  .back-brand-mark { position: absolute; left: 185px; top: 42px; width: 72px; height: 72px; border-radius: 50%; background: var(--brown); }
  .back-sub { position: absolute; left: 90px; width: 200px; top: 146px; text-align: center; font-family: 'Comic Neue', sans-serif; font-weight: 700; font-size: 9.5px; letter-spacing: .6px; color: var(--brown); border-top: 1px solid var(--brown); padding-top: 1px; margin-left: 18px; width: 188px; }
  .appointment { position: absolute; left: 32px; top: 183px; width: 428px; height: 117px; border-radius: 10px; background: rgba(255,255,255,.92); padding: 20px 20px 0 17px; }
  .appointment h2 { font-family: 'Roboto Condensed', sans-serif; font-weight: 700; font-size: 16.5px; color: #2a1a14; margin-bottom: 10px; }
  .field-row { display: flex; align-items: baseline; font-size: 15px; color: #2a1a14; height: 30px; }
  .field-line { flex: 1; border-bottom: 1px dotted #555; height: 1px; margin: 0 0 3px 1px; }
  .tagline-1 { position: absolute; left: 50px; width: 400px; top: 323px; text-align: center; font-family: 'Comic Neue', sans-serif; font-style: italic; font-weight: 700; font-size: 15.5px; color: var(--brown); border-bottom: 1px solid var(--brown); }
  .tagline-2 { position: absolute; left: 36px; width: 426px; top: 342px; text-align: center; font-family: 'Roboto Condensed', sans-serif; font-style: italic; font-weight: 700; font-size: 19px; color: var(--brown); white-space: nowrap; }
</style>
</head>
<body>

<section class="card card-front">
  <div class="brand-mark"></div>
  <div class="brand-name">Brindle Oaks Orthodontics</div>
  <div class="brand-sub">Pediatric Dentistry &amp; Orthodontics</div>

  <div class="doctor-name">Dana Whitlock</div>
  <div class="divider"></div>
  <ul class="contact">
    <li><svg viewBox="0 0 12 12"><path d="M6 0a4.2 4.2 0 0 0-4.2 4.2C1.8 7.4 6 12 6 12s4.2-4.6 4.2-7.8A4.2 4.2 0 0 0 6 0zm0 6a1.8 1.8 0 1 1 0-3.6A1.8 1.8 0 0 1 6 6z"/></svg><span>123 Street Name<br>City, State Zip code</span></li>
    <li><svg viewBox="0 0 12 12"><path d="M2.4 0.6l2 2.2-1 1.4c.7 1.6 2 2.9 3.5 3.6l1.4-1 2.2 2-1.2 1.9C4.6 10.6 1.2 7.2.6 2.6z"/></svg><span>555-201-4730</span></li>
    <li><svg viewBox="0 0 12 12"><path d="M0 2h12v8H0z M0.8 2.6 6 6.6l5.2-4" stroke="#fff" stroke-width=".9"/></svg><span>office@brindleoaksortho.com</span></li>
  </ul>

  <svg class="wave" viewBox="0 0 686 112" preserveAspectRatio="none">
    <defs>
      <linearGradient id="bandFill" x1="0" y1="0" x2="1" y2="0">
        <stop offset="0" stop-color="#3a8aa3"/>
        <stop offset="1" stop-color="#57a9bf"/>
      </linearGradient>
    </defs>
    <path d="M0 13 Q330 78 686 22 L686 112 L0 112 Z" fill="url(#bandFill)"/>
    <path d="M0 13 Q330 78 686 22" fill="none" stroke="#7fd0bd" stroke-width="4"/>
  </svg>
  <div class="website">www.brindleoaksortho.com</div>
</section>

<section class="card card-back">
  <div class="beach-scene" role="img" aria-label="Illustrated tropical island beach with palm trees, a rocky peak, clouds, blue sea, sand, and a small street map showing the office location"></div>
  <div class="back-brand-mark"></div>
  <div class="back-brand">Brindle Oaks Orthodontics</div>
  <div class="back-sub">Pediatric Dentistry &amp; Orthodontics</div>

  <div class="appointment">
    <h2>SEE YOU AT YOUR NEXT APPOINTMENT!</h2>
    <div class="field-row">For<span class="field-line"></span></div>
    <div class="field-row">Date<span class="field-line"></span>Time<span class="field-line"></span></div>
  </div>

  <div class="tagline-1">Specialist in Orthodontic &amp; Maxillofacial Orthopedics</div>
  <div class="tagline-2">Creating "Tolvering" smiles for Children &amp; Adults</div>
</section>

</body>
</html>
```